Advertising company unique advertising platform

we need a logo design for a new company based in Australia Melbourne. We develop innovated advertising platform where consumer can use this platform to get regular discount, as business owner they can use this platform for free advertisement. Payment for this advertisement platform only payable every two weeks, when I generate revenue for their business

Industry/Entity Type

Advertising

Contact Information for Business Card

Dale Morven | Co-Founder |Managing Director
Suite 718 240 Wattlebrook Lane Melbourne Vic 3000

ABN 38 614 207 923
Tel: +61 0487 259 318 | Email: dale.morven@plivorantu.com

Font styles to use
Decorative
Script

Requirements
Must have
• Try few different design and some round corner business card
Should not have
• One round corner business card...try 4 different colour background not only black, make sure two side is designed. Be creative so imagine you are giving this to a client make sure has wow factor, if you can also try one design with engrave like all the logo, words look 3d feel
• The word Advertising Platform use attached file font

```html
<!DOCTYPE html>
<html lang="en">
<head>
<meta charset="utf-8">
<title>Kestrova Loop – Business Card</title>
<link rel="stylesheet" href="https://fonts.googleapis.com/css2?family=Marcellus&family=Montserrat:wght@400;500;700&display=swap">
<style>
  :root {
    --canvas: #ece9e4;
    --card-light: #ffffff;
    --card-dark: #2b2b2b;
    --card-dark-edge: #1f1f1f;
    --accent: #f08a24;
    --text-light: #f2f2f2;
    --text-muted: #d6d6d6;
    --shadow: rgba(0, 0, 0, 0.18);
  }
  * { box-sizing: border-box; margin: 0; padding: 0; }
  html, body {
    width: 1200px;
    height: 900px;
    overflow: hidden;
    background: var(--canvas);
  }
  .canvas {
    position: relative;
    width: 1200px;
    height: 900px;
  }
  .card {
    position: absolute;
    left: 320px;
    width: 560px;
    height: 320px;
    border-radius: 24px;
    box-shadow: 0 14px 30px var(--shadow);
    overflow: hidden;
  }
  .card--front {
    top: 100px;
    background: var(--card-light);
    display: flex;
    align-items: center;
    justify-content: center;
  }
  .card--back {
    top: 480px;
    background: linear-gradient(135deg, #353535 0%, var(--card-dark) 45%, var(--card-dark-edge) 100%);
  }
  .brand {
    display: flex;
    align-items: center;
    gap: 14px;
  }
  .brand__dot {
    width: 22px;
    height: 22px;
    border-radius: 50%;
    background: var(--accent);
  }
  .brand__name {
    font-family: "Montserrat", sans-serif;
    font-weight: 700;
    font-size: 38px;
    color: var(--accent);
    letter-spacing: 1px;
  }
  .card--back .brand {
    position: absolute;
    left: 42px;
    top: 190px;
  }
  .card--back .brand__name { font-size: 28px; }
  .card--back .brand__dot { width: 18px; height: 18px; }

  .identity {
    position: absolute;
    left: 300px;
    top: 60px;
    padding-left: 18px;
    border-left: 2px solid var(--text-light);
  }
  .identity__name {
    font-family: "Marcellus", serif;
    font-size: 30px;
    color: var(--accent);
    letter-spacing: 1px;
    text-transform: uppercase;
    line-height: 1.1;
  }
  .identity__role {
    font-family: "Marcellus", serif;
    font-size: 11px;
    color: var(--text-light);
    letter-spacing: 0.5px;
    text-transform: uppercase;
    margin-top: 4px;
  }
  .contact {
    position: absolute;
    left: 300px;
    top: 150px;
    padding-left: 18px;
    border-left: 2px solid var(--accent);
    font-family: "Montserrat", sans-serif;
    font-size: 13px;
    color: var(--text-muted);
    line-height: 1.55;
    list-style: none;
  }
  .contact__item {
    display: flex;
    align-items: center;
    gap: 8px;
  }
  .contact__label { color: var(--accent); }
  .contact__icon {
    width: 12px;
    height: 12px;
    flex: none;
  }
</style>
</head>
<body>
<main class="canvas">
  <section class="card card--front" aria-label="Card front">
    <div class="brand">
      <span class="brand__dot"></span>
      <span class="brand__name">Kestrova Loop</span>
    </div>
  </section>

  <section class="card card--back" aria-label="Card back">
    <div class="brand">
      <span class="brand__dot"></span>
      <span class="brand__name">Kestrova Loop</span>
    </div>

    <header class="identity">
      <h1 class="identity__name">Dale Morven</h1>
      <p class="identity__role">Co-Founder | Managing Director</p>
    </header>

    <ul class="contact">
      <li class="contact__item">Suite 718 240 Wattlebrook</li>
      <li class="contact__item">Lane Melbourne Vic 3000</li>
      <li class="contact__item"><span><span class="contact__label">ABN:</span> 38 614 207 923</span></li>
      <li class="contact__item">
        <svg class="contact__icon" viewBox="0 0 24 24" aria-hidden="true">
          <path fill="#f08a24" d="M6.6 10.8a15.1 15.1 0 0 0 6.6 6.6l2.2-2.2a1 1 0 0 1 1-.25 11.4 11.4 0 0 0 3.6.57 1 1 0 0 1 1 1V20a1 1 0 0 1-1 1A17 17 0 0 1 3 4a1 1 0 0 1 1-1h3.5a1 1 0 0 1 1 1c0 1.25.2 2.45.57 3.6a1 1 0 0 1-.25 1z"/>
        </svg>
        +61 0487 259 318
      </li>
      <li class="contact__item">
        <svg class="contact__icon" viewBox="0 0 24 24" aria-hidden="true">
          <rect x="2.5" y="5" width="19" height="14" rx="2" fill="none" stroke="#f08a24" stroke-width="2"/>
          <path d="M3 6l9 7 9-7" fill="none" stroke="#f08a24" stroke-width="2"/>
        </svg>
        dale.morven@plivorantu.com
      </li>
    </ul>
  </section>
</main>
</body>
</html>
```